Business Card for Lantern Reach

Please design a Modern Business card for a Online Marketing Company

Website: http://www.lanternreach-example.com.au

Please do NOT include physical address in design.

```html
<!DOCTYPE html>
<html lang="en">
<head>
<meta charset="utf-8">
<title>Lantern Reach – Business Card</title>
<link rel="stylesheet" href="https://fonts.googleapis.com/css2?family=Open+Sans:wght@400;600;700&family=Roboto:wght@700;900&display=swap">
<style>
  :root {
    --backdrop: #ece8e4;
    --card-dark: #23272b;
    --card-dark-glow: #3a4148;
    --brand-red: #c4101a;
    --brand-red-deep: #a70d16;
    --accent-orange: #f07f12;
    --ink-light: #ffffff;
    --ink-muted: #c9ccd0;
    --ink-soft: #9aa0a6;
    --ink-web: #f3e3e4;
  }
  * { box-sizing: border-box; margin: 0; padding: 0; }
  html, body { width: 1200px; height: 482px; overflow: hidden; }
  body {
    background: var(--backdrop);
    font-family: "Open Sans", Arial, sans-serif;
    position: relative;
  }
  .card {
    position: absolute;
    top: 76px;
    width: 540px;
    height: 330px;
    border-radius: 3px;
    box-shadow: 0 10px 28px rgba(0,0,0,.25);
    overflow: hidden;
  }
  /* Front */
  .card--front {
    left: 30px;
    background: radial-gradient(ellipse at 55% 55%, var(--card-dark-glow) 0%, var(--card-dark) 65%);
    color: var(--ink-light);
  }
  .contact-list {
    position: absolute;
    top: 34px;
    right: 26px;
    list-style: none;
    text-align: right;
  }
  .contact-item {
    display: flex;
    align-items: center;
    justify-content: flex-end;
    gap: 12px;
    font-size: 13px;
    color: var(--ink-muted);
    height: 30px;
    margin-bottom: 12px;
  }
  .contact-icon {
    width: 30px; height: 30px;
    border-radius: 5px;
    display: flex; align-items: center; justify-content: center;
    background: var(--brand-red);
  }
  .contact-icon--phone { background: var(--accent-orange); }
  .contact-icon svg { width: 17px; height: 17px; }
  .holder {
    position: absolute;
    left: 34px;
    top: 138px;
  }
  .holder-name { font-size: 19px; font-weight: 700; }
  .holder-title { font-size: 13px; color: var(--ink-soft); margin-top: 2px; }
  .brand-lockup {
    position: absolute;
    left: 34px;
    bottom: 36px;
  }
  .brand-row { display: flex; align-items: center; gap: 10px; }
  .brand-square {
    width: 24px; height: 24px;
    background: var(--brand-red);
    border-radius: 3px;
  }
  .brand-name {
    font-family: "Roboto", Arial, sans-serif;
    font-weight: 900;
    font-size: 20px;
    color: var(--brand-red);
    letter-spacing: .3px;
  }
  .brand-tagline {
    font-family: "Roboto", Arial, sans-serif;
    font-weight: 700;
    font-size: 11px;
    color: var(--ink-light);
    margin: 3px 0 0 34px;
  }
  /* Back */
  .card--back {
    left: 630px;
    background: linear-gradient(160deg, var(--brand-red) 0%, var(--brand-red-deep) 100%);
    color: var(--ink-light);
    text-align: center;
    font-family: "Roboto", Arial, sans-serif;
  }
  .back-name {
    margin-top: 108px;
    font-size: 42px;
    font-weight: 900;
    letter-spacing: .5px;
    text-transform: uppercase;
  }
  .back-tagline {
    font-size: 19px;
    font-weight: 700;
    margin-top: 4px;
  }
  .back-web {
    position: absolute;
    left: 0; right: 0; bottom: 44px;
    font-family: "Open Sans", Arial, sans-serif;
    font-size: 17px;
    font-weight: 600;
    color: var(--ink-web);
  }
</style>
</head>
<body>
  <section class="card card--front" aria-label="Business card front">
    <ul class="contact-list">
      <li class="contact-item">0400 123 456
        <span class="contact-icon contact-icon--phone">
          <svg viewBox="0 0 24 24" fill="#fff"><path d="M6.6 10.8a15 15 0 0 0 6.6 6.6l2.2-2.2a1 1 0 0 1 1-.25 11.4 11.4 0 0 0 3.6.57 1 1 0 0 1 1 1V20a1 1 0 0 1-1 1A17 17 0 0 1 3 4a1 1 0 0 1 1-1h3.5a1 1 0 0 1 1 1c0 1.25.2 2.45.57 3.57a1 1 0 0 1-.25 1z"/></svg>
        </span>
      </li>
      <li class="contact-item">www.lanternreach-example.com.au
        <span class="contact-icon">
          <svg viewBox="0 0 24 24" fill="none" stroke="#fff" stroke-width="1.6"><circle cx="12" cy="12" r="9"/><ellipse cx="12" cy="12" rx="4" ry="9"/><path d="M3 12h18M5 7h14M5 17h14"/></svg>
        </span>
      </li>
      <li class="contact-item">plan@lanternreach-example.com.au
        <span class="contact-icon">
          <svg viewBox="0 0 24 24" fill="none" stroke="#fff" stroke-width="1.6"><rect x="3" y="6" width="18" height="12" rx="1"/><path d="M3 6l9 7 9-7"/></svg>
        </span>
      </li>
    </ul>
    <div class="holder">
      <p class="holder-name">Your Name</p>
      <p class="holder-title">Title</p>
    </div>
    <div class="brand-lockup">
      <div class="brand-row">
        <span class="brand-square"></span>
        <span class="brand-name">LANTERN REACH</span>
      </div>
      <p class="brand-tagline">Get seen online - Grow online</p>
    </div>
  </section>

  <section class="card card--back" aria-label="Business card back">
    <p class="back-name">Lantern Reach</p>
    <p class="back-tagline">Get seen online - Grow online</p>
    <p class="back-web">www.lanternreach-example.com.au</p>
  </section>
</body>
</html>
```